Venture 482 - Lumora Book Cover

I am looking for a Lumora book cover for my book about "Venture 482".
The Book is Titled:
Venture 482 Ascended
Shaping Outcomes: Paths To Unlocking Cosmic Truths
Author is Dorian Pell
Here is a book description that may help you understand more about it:
Inspired by the genius of Edwin Marlowe, this comprehensive guide delves into the ancient wisdom and cutting-edge science behind the 482 method, a powerful tool for manifesting your desires. Whether you're seeking personal growth, financial success, or spiritual enlightenment, this book provides advanced techniques and methods to transform your dreams into reality.
Any questions please ask.
Thanks
Owen

```html
<!DOCTYPE html>
<html lang="en">
<head>
<meta charset="utf-8">
<title>Venture 482 Ascended — Dorian Pell</title>
<link rel="stylesheet" href="https://fonts.googleapis.com/css2?family=Cinzel:wght@400;500&family=Tinos&display=swap">
<style>
  :root {
    --night: #07101f;
    --deep-blue: #0d2440;
    --glow-teal: #2f8fb0;
    --glow-gold: #c9a64a;
    --author-blush: #f1d5cb;
    --title-cream: #f8ebe1;
    --subtitle-white: #f4f1ee;
  }
  html, body {
    margin: 0;
    padding: 0;
    overflow: hidden;
    background: var(--night);
  }
  .cover {
    position: relative;
    width: 805px;
    height: 1200px;
    overflow: hidden;
    background: var(--night);
  }
  .cover-art {
    position: absolute;
    inset: 0;
    background:
      radial-gradient(ellipse 90px 260px at 402px 430px, rgba(201,166,74,0.45), transparent 70%),
      radial-gradient(ellipse 300px 520px at 402px 520px, rgba(47,143,176,0.55), transparent 72%),
      radial-gradient(ellipse 520px 700px at 402px 560px, rgba(20,60,100,0.7), transparent 75%),
      linear-gradient(180deg, #0a1628 0%, var(--deep-blue) 45%, #091a30 100%);
  }
  .author {
    position: absolute;
    top: 70px;
    left: 0;
    width: 100%;
    margin: 0;
    text-align: center;
    font-family: "Cinzel", serif;
    font-weight: 400;
    font-size: 58px;
    letter-spacing: 0.32em;
    text-indent: 0.32em;
    color: var(--author-blush);
    line-height: 1;
  }
  .title {
    position: absolute;
    top: 545px;
    left: 0;
    width: 100%;
    margin: 0;
    text-align: center;
    color: var(--title-cream);
    font-family: "Cinzel", serif;
    font-weight: 400;
  }
  .title-word {
    display: block;
    font-size: 122px;
    line-height: 1;
    letter-spacing: -0.01em;
  }
  .title-number {
    display: block;
    font-size: 285px;
    line-height: 0.8;
    margin-top: 6px;
    letter-spacing: -0.04em;
  }
  .title-edition {
    display: block;
    margin-top: 18px;
    font-size: 64px;
    line-height: 1;
    letter-spacing: 0.42em;
    text-indent: 0.42em;
    text-shadow: 3px 3px 4px rgba(0,0,0,0.9);
  }
  .subtitle {
    position: absolute;
    top: 996px;
    left: 0;
    width: 100%;
    margin: 0;
    text-align: center;
    font-family: "Tinos", serif;
    color: var(--subtitle-white);
  }
  .subtitle-lead {
    display: block;
    font-size: 28px;
    line-height: 1.2;
    letter-spacing: 0.01em;
  }
  .subtitle-line {
    display: block;
    font-size: 26px;
    line-height: 40px;
  }
  .subtitle-lead + .subtitle-line { margin-top: 14px; }
</style>
</head>
<body>
  <main class="cover">
    <div class="cover-art" role="img" aria-label="Glowing outline of a human figure with arms spread, made of tangled blue and gold energy threads against a dark starry night sky"></div>
    <p class="author">DORIAN PELL</p>
    <h1 class="title">
      <span class="title-word">Venture</span>
      <span class="title-number">482</span>
      <span class="title-edition">ASCENDED</span>
    </h1>
    <p class="subtitle">
      <span class="subtitle-lead">SHAPING OUTCOMES:</span>
      <span class="subtitle-line">Paths to unlocking</span>
      <span class="subtitle-line">cosmic truths</span>
    </p>
  </main>
</body>
</html>
```